1 Dimensional cover for digital product

Please note that if a designer comes in with an original design and other designers try to copy them too closely I will always work with the original designer in order to get the actual look I want.
Therefore it is in the interests of the designers to get their concepts in first.

I am designing some audio products for football (soccer players).

I would like a square version and a 16:9 version of the packaging completed. The square version will be for the Sonvia audio cover and the 16:9 for the thumbnails of videos.

I would like the final images in PSP files as a template that I can change the title and the main image.

I am open to creativity in this project but would like it to be a luxury and premium in what it is portraying.

I have added my logo and also the packaging that I currently use on my sister website which is not aimed at football, soccer.

I've also included an image of one of my models. This would NOT be the product image, but it could be a background image, or you may choose to leave it out altogether.

I've also included an example image as the main product image.

Although I have chosen greyscale I would also like to see products with colour.

The product page is at https://kelvarn.global/collections/all
I add this so that you can chose any one of the titles for this template

Target Market(s)

This is aimed at professional footballers

Industry/Entity Type

Sporting Good

Font styles to use
Serif
Sans Serif

Colors

Designer to choose colors to be used in the design.

Requirements
Must have
• This must look like it is made for an affluent market.
• It may also be simple in its design but I do not wish to be too prescriptive with creativity.
• My typography is Montserrat
Nice to have
• Can include the colors of my logos:
• #5BA9DE
• #272B5F
• Or you can choose to go with greyscale
Should not have
• This is a product for serious athletes so it should look very professional and adult orientated (so not cartoonish its look)

```html
<!DOCTYPE html>
<html lang="en">
<head>
<meta charset="utf-8">
<title>Stress Relief – Hypnosis Sessions</title>
<link rel="stylesheet" href="https://fonts.googleapis.com/css2?family=Montserrat:wght@400;600;700&display=swap">
<style>
  :root {
    --brand-blue: #5BA9DE;
    --brand-navy: #272B5F;
    --gold: #B3A46A;
    --ink: #070708;
    --badge-grey: #c3c4c6;
    --photo-grey: #5a5c60;
    --photo-steel: #3f5468;
    --photo-light: #dbe5ee;
  }
  * { margin: 0; padding: 0; box-sizing: border-box; }
  html, body { width: 1200px; height: 675px; overflow: hidden; background: var(--ink); }
  .cover {
    position: relative;
    width: 1200px;
    height: 675px;
    overflow: hidden;
    font-family: "Montserrat", sans-serif;
    background: linear-gradient(125deg, #030303 0%, #121314 40%, #2a2b2e 70%, #1a1b1d 100%);
  }
  .hero-photo {
    position: absolute;
    inset: 0;
    clip-path: polygon(773px 0, 1200px 0, 1200px 675px, 102px 675px);
    background:
      radial-gradient(ellipse 150px 90px at 880px 660px, rgba(255,255,255,0.95) 0%, rgba(230,238,246,0.5) 40%, transparent 100%),
      radial-gradient(ellipse 260px 300px at 1060px 330px, rgba(235,242,248,0.75) 0%, rgba(190,206,220,0.35) 45%, transparent 100%),
      radial-gradient(ellipse 300px 220px at 1150px 120px, rgba(200,214,228,0.55) 0%, transparent 100%),
      radial-gradient(ellipse 140px 230px at 700px 440px, rgba(120,122,126,0.7) 0%, transparent 100%),
      linear-gradient(90deg, #3b3c3f 0%, var(--photo-grey) 45%, #4d5a68 62%, var(--photo-steel) 80%, #2e3c4b 100%);
  }
  .brand-badge {
    position: absolute; top: 0; left: 0;
    width: 320px; height: 200px;
  }
  .brand-name {
    position: absolute;
    top: 52px; left: 26px;
    width: 200px;
    text-align: center;
    color: var(--brand-navy);
    font-weight: 600;
    font-size: 9px;
    letter-spacing: 0.3px;
    line-height: 1.7;
  }
  .brand-name .dot {
    display: block;
    width: 16px; height: 16px;
    margin: 0 auto 8px;
    border-radius: 50%;
    background: var(--brand-blue);
  }
  .brand-name .wordmark { font-size: 13px; letter-spacing: 1.5px; }
  .eyebrow {
    position: absolute;
    left: 172px; top: 221px;
    color: var(--brand-blue);
    font-weight: 600;
    font-size: 19px;
  }
  .title {
    position: absolute;
    left: 162px; top: 251px;
    width: 480px;
    color: var(--brand-blue);
    font-weight: 700;
    font-size: 122px;
    line-height: 0.85;
    letter-spacing: -1px;
    text-align: center;
  }
  .edition {
    position: absolute;
    left: 231px; top: 493px;
    display: flex; align-items: center;
  }
  .edition .diamond {
    width: 34px; height: 34px;
    margin: 7px;
    background: var(--gold);
    transform: rotate(45deg);
  }
  .edition .label {
    margin-left: 19px;
    color: var(--gold);
    font-weight: 400;
    font-size: 15px;
    letter-spacing: 0.3px;
  }
  .tagline {
    position: absolute;
    left: 232px; top: 556px;
    color: var(--brand-blue);
    font-weight: 400;
    font-size: 13px;
    letter-spacing: 0.2px;
  }
</style>
</head>
<body>
  <main class="cover">
    <div class="hero-photo" role="img" aria-label="Photograph: two footballers in mid-air under stadium floodlights — one volleying in a dark kit, one in white rising to head the ball against a stormy sky"></div>

    <svg class="brand-badge" viewBox="0 0 320 200" aria-hidden="true">
      <polygon points="0,0 316,0 118,197 0,78" fill="var(--badge-grey)"/>
    </svg>
    <div class="brand-name">
      <span class="dot"></span>
      ELIAS CORWIN HYPNOTHERAPY<br>
      <span class="wordmark">KELVARN</span>
    </div>

    <p class="eyebrow">Hypnosis sessions</p>
    <h1 class="title">STRESS<br>RELIEF</h1>

    <div class="edition">
      <span class="diamond"></span>
      <span class="label">TRIPLE IMPACT EDITION</span>
    </div>

    <p class="tagline">CONDITION YOURSELF TO MANAGE A STRESSFUL LIFE</p>
  </main>
</body>
</html>
```